Flaschenetiketten-Design in rechteckiger Grundform für Biermanufaktur
Zielgruppe
Wir repräsentieren eine Bier-Manufaktur in der Gründungsphase und sind auf der Suche nach einem Designvorschlag für die Flaschenetiketten.
Unsere Zielgruppe sind Liebhaber, die auf der Suche nach dem Speziellen und Lokalen sind. Der Biergenuss abseits des Massenmarktes soll im Entwurf sichtbar/transportiert werden. Die Bier-Manufaktur steht zeitgleich für Trend-Kreationen mit bodenständigem Ursprung.
Aufgabenstellung
Die Herkunft der Gründer Familie aus dem Schweizer Kanton Simplon soll im Vordergrund stehen, hierzu bitte das Familienwappen / einzelne Elemente siehe Dateiupload berücksichtigen.
Das Etikett soll eine rechteckige Grundform haben.
Folgende Angaben sollen sich im Etikett wiederfinden:
- Biersorte: 'Lager' (zukünftig soll es möglich sein, Biersorte auf dem Etikett zu wechseln)
Brand: 'Hearty Kandrom'
'Biermanufaktur Walliser Ursprungs'
Die Schrift soll klar und nicht zu verspielt sein.

```html
<!DOCTYPE html>
<html lang="de">
<head>
<meta charset="utf-8">
<title>Hearty Kandrom – Flaschenetikett Lager</title>
<link href="https://fonts.googleapis.com/css2?family=Oswald:wght@700&family=Fira+Sans:wght@400&display=swap" rel="stylesheet">
<style>
  :root {
    --stage: #f1f1f1;
    --label-paper: #f4f4f4;
    --gold-light: #f3d77a;
    --gold-mid: #d9a521;
    --gold-dark: #a9780f;
    --royal-blue: #1f5aa6;
    --deep-blue: #123f86;
    --glow-blue: #4f8fd6;
    --hop-grey: #dcdcdc;
    --text-white: #ffffff;
  }
  * { margin: 0; padding: 0; box-sizing: border-box; }
  html, body {
    width: 1200px;
    height: 803px;
    overflow: hidden;
    background: var(--stage);
  }
  .stage {
    position: relative;
    width: 1200px;
    height: 803px;
    display: flex;
    align-items: center;
    justify-content: center;
  }
  .bottle-label {
    width: 675px;
    height: 720px;
    display: block;
    box-shadow: 0 6px 18px rgba(0,0,0,0.12);
  }
  .brand-name {
    font-family: "Oswald", "Arial Narrow", sans-serif;
    font-weight: 700;
    fill: var(--text-white);
    letter-spacing: 1px;
  }
  .origin-line {
    font-family: "Fira Sans", Arial, sans-serif;
    font-weight: 400;
    fill: var(--text-white);
  }
</style>
</head>
<body>
<main class="stage">
  <svg class="bottle-label" viewBox="0 0 672 717" xmlns="http://www.w3.org/2000/svg" aria-labelledby="label-title">
    <title id="label-title">Hearty Kandrom – Biermanufaktur Walliser Ursprungs</title>
    <defs>
      <linearGradient id="gold-band" x1="0" x2="1" y1="0" y2="0">
        <stop offset="0" stop-color="var(--gold-mid)"/>
        <stop offset="0.45" stop-color="var(--gold-dark)"/>
        <stop offset="0.7" stop-color="var(--gold-light)"/>
        <stop offset="1" stop-color="var(--gold-mid)"/>
      </linearGradient>
      <linearGradient id="gold-frame" x1="0" x2="1" y1="0" y2="1">
        <stop offset="0" stop-color="var(--gold-light)"/>
        <stop offset="0.5" stop-color="var(--gold-mid)"/>
        <stop offset="1" stop-color="var(--gold-dark)"/>
      </linearGradient>
      <radialGradient id="blue-field" cx="0.6" cy="0.42" r="0.65">
        <stop offset="0" stop-color="var(--glow-blue)"/>
        <stop offset="0.55" stop-color="var(--royal-blue)"/>
        <stop offset="1" stop-color="var(--deep-blue)"/>
      </radialGradient>
    </defs>

    <!-- paper -->
    <rect class="label-paper" width="672" height="717" fill="var(--label-paper)"/>

    <!-- gold bands -->
    <rect class="gold-band gold-band--top" x="0" y="0" width="672" height="22" fill="url(#gold-band)"/>
    <rect class="gold-band gold-band--bottom" x="0" y="695" width="672" height="22" fill="url(#gold-band)"/>

    <!-- hop leaf decoration area -->
    <rect class="hop-decoration" x="50" y="600" width="572" height="95" rx="40"
          fill="var(--hop-grey)" opacity="0.6"
          role="img" aria-label="Dezentes graues Hopfenblatt-Ornament"/>

    <!-- baroque frame area -->
    <ellipse class="baroque-frame" cx="334" cy="380" rx="240" ry="260"
             fill="url(#gold-frame)"
             role="img" aria-label="Goldener barocker Zierrahmen mit Akanthusranken"/>

    <!-- blue oval field -->
    <ellipse class="brand-field" cx="340" cy="378" rx="172" ry="222"
             fill="url(#blue-field)" stroke="var(--gold-dark)" stroke-width="6"/>

    <!-- family crest area -->
    <rect class="family-crest" x="272" y="58" width="132" height="160" rx="8"
          fill="var(--royal-blue)" stroke="var(--gold-mid)" stroke-width="6"
          role="img" aria-label="Familienwappen mit Sternen, Reichsapfel und grünem Dreiberg"/>

    <!-- brand -->
    <text class="brand-name" x="338" y="330" text-anchor="middle" font-size="104">HEARTY</text>
    <text class="brand-name" x="338" y="445" text-anchor="middle" font-size="104">KANDROM</text>

    <!-- origin line -->
    <text class="origin-line" x="338" y="487" text-anchor="middle" font-size="22">Biermanufaktur Walliser</text>
    <text class="origin-line" x="338" y="513" text-anchor="middle" font-size="22">Ursprungs</text>
  </svg>
</main>
</body>
</html>
```